BOLD & MINIMALIST DESIGN NEEDED

We want a very bold but minimalistic business card design that is impactful and utilizes both sides of the business card. Our current logo is included for your use.

We want bold fonts and good use of negative space. We don't want the logo to overpower the design.

Target Market(s)

Professionals who are building new commercial buildings.

Industry/Entity Type

Construction

Contact Information for Business Card

Name, Title, email, office phone, cell phone, website

Font styles to use
Serif
Sans Serif

Requirements
Must have
• Bold design!

```html
<!DOCTYPE html>
<html lang="en">
<head>
<meta charset="utf-8">
<title>Ridgemont Design + Build – Business Card</title>
<link href="https://fonts.googleapis.com/css2?family=Lato:wght@400;700;900&display=swap" rel="stylesheet">
<style>
  :root {
    --stage: #2b2b2b;
    --green: #6fa81f;
    --green-bright: #86c22a;
    --green-deep: #2f5411;
    --green-mid: #4f7a19;
    --ink: #111111;
    --paper: #ffffff;
    --text: #1a1a1a;
  }
  * { margin: 0; padding: 0; box-sizing: border-box; }
  html, body { width: 1200px; height: 800px; overflow: hidden; }
  body {
    background: var(--stage);
    font-family: "Lato", Arial, sans-serif;
    position: relative;
  }
  .card {
    position: absolute;
    width: 560px;
    height: 320px;
    border-radius: 18px;
    overflow: hidden;
  }
  /* Front side */
  .card-front {
    left: 80px; top: 60px;
    background: radial-gradient(circle at 40% 30%, var(--green-mid) 0%, var(--green-deep) 80%);
  }
  .front-brand {
    position: absolute;
    left: 50px; top: 118px;
    color: var(--paper);
  }
  .brand-name {
    display: flex; align-items: center; gap: 10px;
    font-weight: 900; font-size: 36px; letter-spacing: 0.5px; line-height: 1;
  }
  .brand-mark {
    width: 16px; height: 16px; background: var(--green-bright);
  }
  .brand-tag {
    margin-top: 8px; margin-left: 26px;
    font-weight: 400; font-size: 11px; letter-spacing: 6px;
  }
  .feature-block {
    position: absolute;
    top: 0; right: 0; bottom: 0;
    width: 250px;
    background: linear-gradient(135deg, var(--ink) 0%, var(--ink) 40%, var(--green-bright) 75%, #b8e07a 100%);
  }
  /* Back side */
  .card-back {
    left: 560px; top: 420px;
    background: var(--paper);
  }
  .card-back .feature-block {
    bottom: 40px;
    width: 230px;
  }
  .back-brand {
    position: absolute; left: 34px; top: 34px; color: var(--ink);
  }
  .back-brand .brand-name { font-size: 28px; }
  .back-brand .brand-mark { width: 13px; height: 13px; background: var(--green); }
  .back-brand .brand-tag { font-size: 9px; letter-spacing: 5px; margin-left: 23px; }
  .person { position: absolute; left: 34px; top: 108px; }
  .person-name { color: var(--green); font-weight: 900; font-size: 26px; }
  .person-title { color: var(--text); font-size: 14px; margin-top: 2px; }
  .contact-list { list-style: none; margin-top: 12px; }
  .contact-list li {
    display: flex; align-items: center; gap: 10px;
    font-size: 14px; color: var(--text); line-height: 22px;
  }
  .contact-list svg { width: 14px; height: 14px; fill: var(--green); flex: none; }
  .address-band {
    position: absolute; left: 0; right: 0; bottom: 0; height: 40px;
    background: var(--green);
    color: var(--paper);
    display: flex; align-items: center; justify-content: flex-end; gap: 8px;
    padding-right: 26px;
    font-weight: 700; font-size: 14px;
  }
  .address-band svg { width: 12px; height: 16px; fill: var(--paper); }
</style>
</head>
<body>

<section class="card card-front" aria-label="Card front">
  <div class="front-brand">
    <div class="brand-name"><span class="brand-mark"></span>RIDGEMONT</div>
    <div class="brand-tag">DESIGN + BUILD</div>
  </div>
  <div class="feature-block" role="img" aria-label="Large brand symbol decoration in black and green"></div>
</section>

<section class="card card-back" aria-label="Card back">
  <div class="back-brand">
    <div class="brand-name"><span class="brand-mark"></span>RIDGEMONT</div>
    <div class="brand-tag">DESIGN + BUILD</div>
  </div>
  <div class="person">
    <div class="person-name">Daniel Marsh</div>
    <div class="person-title">Founder &amp; CEO</div>
    <ul class="contact-list">
      <li><svg viewBox="0 0 24 24"><path d="M6.6 10.8a15 15 0 0 0 6.6 6.6l2.2-2.2a1 1 0 0 1 1-.25 11.4 11.4 0 0 0 3.6.57 1 1 0 0 1 1 1V20a1 1 0 0 1-1 1A17 17 0 0 1 3 4a1 1 0 0 1 1-1h3.5a1 1 0 0 1 1 1c0 1.25.2 2.45.57 3.57a1 1 0 0 1-.25 1z"/></svg>012-555-014-372</li>
      <li><svg viewBox="0 0 24 24"><path d="M7 1h10a2 2 0 0 1 2 2v18a2 2 0 0 1-2 2H7a2 2 0 0 1-2-2V3a2 2 0 0 1 2-2zm0 3v14h10V4zm5 15.5a1.2 1.2 0 1 0 0 2.4 1.2 1.2 0 0 0 0-2.4z"/></svg>044-555-019-284</li>
      <li><svg viewBox="0 0 24 24"><path d="M2 21l21-9L2 3v7l15 2-15 2z"/></svg>info@ridgemontbuild.com</li>
      <li><svg viewBox="0 0 24 24"><path d="M12 2a10 10 0 1 0 0 20 10 10 0 0 0 0-20zm6.9 6h-3a15 15 0 0 0-1.3-3.9A8 8 0 0 1 18.9 8zM12 4c.8 1.2 1.5 2.5 1.9 4h-3.8c.4-1.5 1.1-2.8 1.9-4zM4.3 14a8 8 0 0 1 0-4h3.4a16 16 0 0 0 0 4zm.8 2h3a15 15 0 0 0 1.3 3.9A8 8 0 0 1 5.1 16zm3-8h-3a8 8 0 0 1 4.3-3.9A15 15 0 0 0 8.1 8zM12 20c-.8-1.2-1.5-2.5-1.9-4h3.8c-.4 1.5-1.1 2.8-1.9 4zm2.3-6H9.7a14 14 0 0 1 0-4h4.6a14 14 0 0 1 0 4zm.3 5.9a15 15 0 0 0 1.3-3.9h3a8 8 0 0 1-4.3 3.9zm1.7-5.9a16 16 0 0 0 0-4h3.4a8 8 0 0 1 0 4z"/></svg>www.ridgemontbuild.com</li>
    </ul>
  </div>
  <div class="feature-block" role="img" aria-label="Large brand symbol decoration in black and green"></div>
  <div class="address-band">
    <span>4471 Harbor Point Pkwy 210-B, FL 32551</span>
    <svg viewBox="0 0 12 16"><path d="M6 0a6 6 0 0 0-6 6c0 4.5 6 10 6 10s6-5.5 6-10a6 6 0 0 0-6-6zm0 8.5a2.5 2.5 0 1 1 0-5 2.5 2.5 0 0 1 0 5z"/></svg>
  </div>
</section>

</body>
</html>
```